I need a logo design for a new company based in Tucson called "Mindtrail Lee Corwin". I am a psychotherapist that specializes in clinical psychology with athletes and performers. The final design should incorporate the psychology symbol as a watermark. The logo should convey movement and fluidity. "Mindtrail" is a bit of a play on words combining psychology (head) with sports (coach). Other design interests include mid-century, Harold Ames Whitby. I will want to use the logo for business cards, letterhead and marketing brochures. I will put together a website at a later date. I am attaching a file with some pertinent information for the business card. Thank you.
Lee Corwin
mindtrailleecorwin@quillpost.net

Thank you all for the submissions so far.  I have submitted an additional file with a draft of a new design idea.  Since "mindtrail" is a bit of a play on words, I would like to see something with the two "H's" look something like quotation marks.  If the psychology logo is to be included at all, it needs to be less prominent.     Thank you all.  Lee                               

Target Market(s)

1) Adolescent and adult athletes and performers who are looking to increase their level of performance (Sport and Performance Psychology)
2) Adult psychotherapy patients (Clinical psychology)

Industry/Entity Type

Marketing

Colors

Designer to choose colors to be used in the design.

Requirements
Must have
• 1) Since "mindtrail" is a bit of a play on words, The "H's" need to be in a font that looks somewhat like quotation marks.

Nice to have
• Logo on one side. All other info on the backside?

```html
<!DOCTYPE html>
<html lang="en">
<head>
<meta charset="utf-8">
<title>Mindtrail business card options</title>
<link rel="stylesheet" href="https://fonts.googleapis.com/css2?family=Alegreya:ital,wght@1,600&family=Lato:ital,wght@0,400;0,700;1,700;1,900&display=swap">
<style>
  :root {
    --page: #e6e7e9;
    --slate: #4b5455;
    --charcoal: #2b3032;
    --royal: #1414c8;
    --white: #ffffff;
    --mint: #8dd3b0;
    --aqua: #a7eef3;
  }
  * { box-sizing: border-box; margin: 0; padding: 0; }
  html, body { width: 1200px; height: 1000px; overflow: hidden; }
  body { background: var(--page); position: relative; font-family: "Lato", sans-serif; }

  .card {
    position: absolute;
    border-radius: 10px;
    display: flex;
    flex-direction: column;
    align-items: center;
  }
  .card--slate { background: var(--slate); }
  .card--charcoal { background: var(--charcoal); }

  .front { justify-content: center; }
  .brand-name {
    font-family: "Lato", sans-serif;
    font-weight: 900;
    font-size: 64px;
    line-height: 1;
    letter-spacing: 1px;
    color: var(--accent);
  }
  .tagline {
    margin-top: 14px;
    font-weight: 700;
    font-style: italic;
    font-size: 14.5px;
    letter-spacing: 1.6px;
    color: var(--tag);
  }

  .back { padding-top: 70px; }
  .holder {
    font-family: "Alegreya", serif;
    font-style: italic;
    font-weight: 600;
    font-size: 29px;
    line-height: 1;
    letter-spacing: 0.5px;
    color: var(--accent);
  }
  .credential {
    margin-top: 4px;
    font-weight: 700;
    font-size: 13px;
    color: var(--sub);
  }
  .contact { margin-top: 42px; text-align: center; list-style: none; }
  .contact li { font-size: 13px; line-height: 21px; color: var(--value); }
  .contact b { font-weight: 700; color: var(--accent); }

  .theme-royal { --accent: var(--royal); --sub: var(--white); --value: var(--white); --tag: var(--white); }
  .theme-royal .brand-name { color: var(--white); }
  .theme-mint { --accent: var(--mint); --sub: var(--mint); --value: var(--mint); --tag: var(--mint); }
  .theme-aqua { --accent: var(--aqua); --sub: var(--aqua); --value: var(--aqua); --tag: var(--aqua); }
</style>
</head>
<body>

  <section class="card card--slate front theme-royal" style="left:89px;top:42px;width:492px;height:288px;">
    <div class="brand-name">Mindtrail</div>
    <div class="tagline">CLINICAL &amp; PERFORMANCE PSYCHOLOGY</div>
  </section>
  <section class="card card--slate back theme-royal" style="left:610px;top:40px;width:498px;height:291px;">
    <div class="holder">Leland H. Corwin, MA, LLC</div>
    <div class="credential">Licensed Professional Counselor</div>
    <ul class="contact">
      <li><b>Fax:</b> 520.555.0142</li>
      <li><b>Mobile:</b> 520.555.0187</li>
      <li><b>Email:</b> mindtrailleecorwin@quillpost.net</li>
      <li><b>Address:</b> 4170 East Saguaro #210 Tucson,&nbsp; AZ 85716</li>
    </ul>
  </section>

  <section class="card card--charcoal front theme-mint" style="left:89px;top:359px;width:492px;height:288px;">
    <div class="brand-name">Mindtrail</div>
    <div class="tagline">CLINICAL &amp; PERFORMANCE PSYCHOLOGY</div>
  </section>
  <section class="card card--charcoal back theme-mint" style="left:610px;top:359px;width:495px;height:289px;">
    <div class="holder">Leland H. Corwin, MA, LLC</div>
    <div class="credential">Licensed Professional Counselor</div>
    <ul class="contact">
      <li><b>Fax:</b> 520.555.0142</li>
      <li><b>Mobile:</b> 520.555.0187</li>
      <li><b>Email:</b> mindtrailleecorwin@quillpost.net</li>
      <li><b>Address:</b> 4170 East Saguaro #210 Tucson,&nbsp; AZ 85716</li>
    </ul>
  </section>

  <section class="card card--charcoal front theme-aqua" style="left:92px;top:676px;width:489px;height:286px;">
    <div class="brand-name">Mindtrail</div>
    <div class="tagline">CLINICAL &amp; PERFORMANCE PSYCHOLOGY</div>
  </section>
  <section class="card card--charcoal back theme-aqua" style="left:612px;top:675px;width:490px;height:287px;">
    <div class="holder">Leland H. Corwin, MA, LLC</div>
    <div class="credential">Licensed Professional Counselor</div>
    <ul class="contact">
      <li><b>Fax:</b> 520.555.0142</li>
      <li><b>Mobile:</b> 520.555.0187</li>
      <li><b>Email:</b> mindtrailleecorwin@quillpost.net</li>
      <li><b>Address:</b> 4170 East Saguaro #210 Tucson,&nbsp; AZ 85716</li>
    </ul>
  </section>

</body>
</html>
```